OBK Farcoast Logistics Limited

We need the buissnes card to be very exclusive. As we are all young in our company. We need this to be the gate to make our clients feel deep interest for us.

We are focused in as International Trade advisors, and our products go from Oil Tanker Ships to Rubber balls for dogs.

Our Slogan is Making Distant Near.
And our main marketing will be through Internet.

We were stablished in 2009 In Mexico and we also have offices in Hong Kong.
We have representatives in China and Europe.

Target Market(s)

Is every company or Individual that wants to develop an International Project or product development or Logistic service of Goods and people.
Some of our current projects are Ship Brokerage, Mine Brokerage, Real State and Product Pormotional development.

Industry/Entity Type

It Company

Requirements
Must have
• Our Logo and slogan, and make the card accoriding to the logo.
Nice to have
• Our Colors

```html
<!DOCTYPE html>
<html lang="en">
<head>
<meta charset="utf-8">
<title>OBK Farcoast Logistics Limited – Business Card</title>
<link href="https://fonts.googleapis.com/css2?family=Source+Sans+3:wght@400;700&family=Michroma&display=swap" rel="stylesheet">
<style>
  :root{
    --bg:#e9e6e1;
    --card:#161616;
    --green:#8af31c;
    --cyan:#4fd2f0;
    --blue:#2680ff;
    --ring:#3a7ee0;
    --white:#ffffff;
    --text:#e6e6e6;
  }
  html,body{margin:0;padding:0;overflow:hidden}
  body{width:1200px;height:1017px;background:var(--bg);position:relative;font-family:"Source Sans 3",sans-serif}
  .card{position:absolute;top:37px;width:535px;height:937px;background:var(--card);box-shadow:0 2px 6px rgba(0,0,0,.25)}
  .card--front{left:43px}
  .card--back{left:612px}
  .mark-circle{position:absolute;border-radius:50%;border:6px solid var(--ring);box-sizing:border-box}
  .front-circle{width:240px;height:240px;left:147px;top:80px}
  .brand-name{position:absolute;left:0;width:100%;text-align:center;color:var(--green);font-weight:700;margin:0}
  .front-name{top:338px;font-size:96px;line-height:96px;letter-spacing:4px}
  .slogan-small{position:absolute;top:435px;left:0;width:100%;text-align:center;font-family:"Michroma",sans-serif;font-size:16px;color:var(--cyan);margin:0}
  .name-band{position:absolute;top:526px;left:0;width:100%;height:82px;background:var(--blue);text-align:center;color:var(--white)}
  .person-name{margin:0;padding-top:4px;font-size:37px;font-weight:700;line-height:42px}
  .person-title{margin:0;font-size:27px;line-height:30px;color:#f0f0f0}
  .contacts{position:absolute;top:645px;left:0;width:100%;list-style:none;margin:0;padding:0;font-size:28px;color:var(--text)}
  .contacts li{display:flex;justify-content:center;align-items:center;gap:8px;height:39.5px}
  .contacts svg{width:24px;height:24px}
  .address{position:absolute;top:834px;left:0;width:100%;text-align:center;font-size:28px;line-height:37px;color:var(--text);margin:0}
  .back-circle{width:330px;height:330px;left:102px;top:243px}
  .back-name{top:150px;font-size:70px;line-height:70px;letter-spacing:4px}
  .slogan-large{position:absolute;top:598px;left:0;width:100%;text-align:center;font-size:34px;letter-spacing:2px;color:var(--green);margin:0}
  .web-large{position:absolute;top:655px;left:0;width:100%;text-align:center;font-size:30px;letter-spacing:.28em;color:var(--white);margin:0}
</style>
</head>
<body>
  <section class="card card--front">
    <div class="mark-circle front-circle"></div>
    <p class="brand-name front-name">OBK</p>
    <p class="slogan-small">Making Distant Near</p>
    <div class="name-band">
      <p class="person-name">Your Name</p>
      <p class="person-title">Title</p>
    </div>
    <ul class="contacts">
      <li><svg viewBox="0 0 24 24"><circle cx="12" cy="12" r="10" fill="none" stroke="#8af31c" stroke-width="2"/><path d="M8 7c0 5 4 9 9 9l-1-3-2 1c-2-1-3-2-4-4l1-2-3-1z" fill="#8af31c"/></svg>123-456-0789</li>
      <li><svg viewBox="0 0 24 24"><rect x="7" y="4" width="10" height="18" rx="1.5" fill="#8af31c"/><rect x="9" y="7" width="6" height="4" fill="#161616"/><rect x="14" y="1" width="2" height="4" fill="#8af31c"/></svg>123-456-0789</li>
      <li><svg viewBox="0 0 24 24"><path d="M2 10 12 3l10 7v10H2z" fill="#8af31c"/><path d="M2 10l10 7 10-7" fill="none" stroke="#161616" stroke-width="1.5"/></svg>info@farcoasttrade.com</li>
      <li><svg viewBox="0 0 24 24" fill="none" stroke="#8af31c" stroke-width="1.6"><circle cx="12" cy="12" r="10"/><ellipse cx="12" cy="12" rx="4.5" ry="10"/><path d="M2 12h20M4 7h16M4 17h16"/></svg>www.farcoasttrade.com</li>
    </ul>
    <p class="address">Street Name, City Name<br>State Zip Code</p>
  </section>

  <section class="card card--back">
    <p class="brand-name back-name">OBK</p>
    <div class="mark-circle back-circle"></div>
    <p class="slogan-large">MAKING DISTANT NEAR</p>
    <p class="web-large">www.farcoasttrade.com</p>
  </section>
</body>
</html>
```